Business Card Design Project

We are a construction company in Orange County, CA. We need a two sided business card. We would like the back to be our logo with web URL. Front should included Name, title, address, phone, fax and email address.

our address is
627 West Dorrance Blvd, Suite 308
Anaheim, CA 92718

Our logo files are attached.

Construction

```html
<!DOCTYPE html>
<html lang="en">
<head>
<meta charset="utf-8">
<title>Verida Business Card</title>
<link rel="stylesheet" href="https://fonts.googleapis.com/css2?family=Source+Sans+3:wght@400;600;700&display=swap">
<style>
  :root {
    --brand-blue: #124b7e;
    --ink: #3a3a3a;
    --paper: #ffffff;
    --backdrop: #dcdcdc;
    --accent-grey: #b9bcc0;
  }
  * { margin: 0; padding: 0; box-sizing: border-box; }
  html, body {
    width: 960px; height: 1200px; overflow: hidden;
    background: var(--backdrop);
    font-family: "Source Sans 3", Arial, sans-serif;
  }
  .canvas { position: relative; width: 960px; height: 1200px; }
  .card {
    position: absolute; background: var(--paper);
    border-radius: 28px; overflow: hidden;
    box-shadow: 0 4px 10px rgba(0,0,0,0.25);
  }
  .card-front { left: 62px; top: 100px; width: 838px; height: 478px; }
  .card-back { left: 56px; top: 645px; width: 838px; height: 478px; }
  .front-art { position: absolute; inset: 0; }
  .wordmark {
    position: absolute; color: var(--brand-blue);
    font-weight: 700; line-height: 1; letter-spacing: 2px;
  }
  .tagline {
    position: absolute; color: var(--brand-blue);
    font-weight: 600; white-space: nowrap;
  }
  .card-front .wordmark { left: 46px; top: 34px; font-size: 118px; }
  .card-front .tagline { left: 48px; top: 146px; font-size: 17px; letter-spacing: 5.6px; }
  .holder {
    position: absolute; left: 48px; top: 214px;
    color: var(--ink); font-size: 25px; font-weight: 600;
  }
  .holder .title { font-size: 20px; }
  .contact {
    position: absolute; left: 48px; color: var(--ink);
    font-size: 21px; white-space: nowrap;
  }
  .contact b { font-style: italic; font-weight: 700; }
  .contact-phone { top: 286px; }
  .contact-web { top: 324px; }
  .address {
    position: absolute; left: 0; right: 0; top: 421px; text-align: center;
    color: var(--paper); font-size: 24px; white-space: nowrap;
  }
  .card-back .wordmark {
    left: 0; right: 0; top: 140px; text-align: center;
    font-size: 170px; letter-spacing: 4px;
  }
  .card-back .tagline {
    left: 0; right: 0; top: 298px; text-align: center;
    font-size: 23px; letter-spacing: 7.6px;
  }
  .site {
    position: absolute; left: 0; right: 0; top: 399px;
    text-align: center; color: var(--ink);
    font-size: 30px; font-weight: 700;
  }
</style>
</head>
<body>
<main class="canvas">
  <section class="card card-front">
    <svg class="front-art" width="838" height="478" viewBox="0 0 838 478" aria-hidden="true">
      <path d="M560,372 C690,340 780,270 838,200 L838,232 C770,310 680,360 560,372 Z" fill="var(--accent-grey)"/>
      <path d="M0,402 C220,392 420,384 600,380 C700,376 780,320 838,262 L838,478 L0,478 Z" fill="var(--brand-blue)"/>
    </svg>
    <div class="wordmark">VERIDA</div>
    <div class="tagline">BUILD • MANAGE • DELIVER</div>
    <div class="holder">Your Name, <span class="title">Designation</span></div>
    <div class="contact contact-phone"><b>p</b> : 1-234-4567 &nbsp;|&nbsp; <b>f</b> : 1-234-4567</div>
    <div class="contact contact-web"><b>e</b> : info@veridabuild.com &nbsp;|&nbsp; <b>w</b> : www.veridabuild.com</div>
    <div class="address">627 West Dorrance Blvd, Suite 308, Anaheim, CA 92718</div>
  </section>

  <section class="card card-back">
    <div class="wordmark">VERIDA</div>
    <div class="tagline">BUILD • MANAGE • DELIVER</div>
    <div class="site">www.veridabuild.com</div>
  </section>
</main>
</body>
</html>
```